Colin Vardek Business card

Hey there, I’m hoping to have a business card designed. I’m in Real estate and just switched to a new Brokerage called: The Harbourline Property Group

The back could just be the company name maybe or whatever looks good!

I’ve attached some logos of our company and some cards my buddy had done up.

On the card:
Colin Vardek
colinvardek@mailora.com
587-412-9065
colinvardek.ca

Target Market(s)

Home buyers and sellers

Industry/Entity Type

Real Estate

Contact Information for Business Card

just looking for a cool and modern design with my picture on it. I like the idea of Black and red being used.

Requirements
Must have
• all the details provided. I'm open to anything. Just want a professional looking card.

```html
<!DOCTYPE html>
<html lang="en">
<head>
<meta charset="utf-8">
<title>Colin Vardek – Business Card</title>
<link href="https://fonts.googleapis.com/css2?family=Montserrat:wght@300;400;700&display=swap" rel="stylesheet">
<style>
  :root {
    --backdrop: #6f6f6f;
    --card-black: #050505;
    --brand-red: #c8183f;
    --ink-white: #f4f4f4;
  }
  * { margin: 0; padding: 0; box-sizing: border-box; }
  html, body {
    width: 1200px;
    height: 800px;
    overflow: hidden;
    background: var(--backdrop);
    font-family: "Montserrat", Arial, sans-serif;
  }
  .business-card {
    position: absolute;
    left: 75px;
    top: 100px;
    width: 1050px;
    height: 600px;
    background: var(--card-black);
    overflow: hidden;
  }
  .brokerage-mark {
    position: absolute;
    left: 80px;
    top: 238px;
    display: flex;
    align-items: center;
    gap: 22px;
  }
  .brokerage-square {
    width: 26px;
    height: 26px;
    background: var(--brand-red);
    flex-shrink: 0;
  }
  .brokerage-name {
    color: var(--ink-white);
    font-weight: 700;
    font-size: 38px;
    line-height: 1.12;
    letter-spacing: -0.5px;
  }
  .divider {
    position: absolute;
    left: 530px;
    top: 200px;
    width: 3px;
    height: 195px;
    background: var(--brand-red);
    transform: rotate(2deg);
  }
  .agent-name {
    position: absolute;
    left: 590px;
    top: 184px;
    font-size: 36px;
    font-weight: 400;
    color: var(--ink-white);
    letter-spacing: 1px;
    white-space: nowrap;
  }
  .agent-name .surname { color: var(--brand-red); }
  .name-bar {
    position: absolute;
    left: 868px;
    top: 200px;
    right: 0;
    height: 22px;
    background: var(--brand-red);
  }
  .contact-list {
    position: absolute;
    left: 590px;
    top: 262px;
    list-style: none;
  }
  .contact-item {
    display: flex;
    align-items: center;
    gap: 16px;
    height: 46px;
    color: var(--ink-white);
    font-size: 20px;
    font-weight: 400;
    letter-spacing: 0.6px;
  }
  .contact-icon {
    width: 24px;
    height: 24px;
    fill: var(--brand-red);
    flex-shrink: 0;
  }
</style>
</head>
<body>
  <main class="business-card">
    <div class="brokerage-mark">
      <span class="brokerage-square"></span>
      <p class="brokerage-name">The Harbourline<br>Property Group</p>
    </div>

    <span class="divider"></span>

    <h1 class="agent-name">Colin <span class="surname">Vardek</span></h1>
    <span class="name-bar"></span>

    <ul class="contact-list">
      <li class="contact-item">
        <svg class="contact-icon" viewBox="0 0 24 24" aria-hidden="true">
          <path d="M2 5h20v14H2z M3.5 6.5l8.5 6.5 8.5-6.5" fill="var(--brand-red)"/>
          <path d="M3 6.5l9 6.8 9-6.8" fill="none" stroke="var(--card-black)" stroke-width="1.6"/>
        </svg>
        colinvardek@mailora.com
      </li>
      <li class="contact-item">
        <svg class="contact-icon" viewBox="0 0 24 24" aria-hidden="true">
          <path d="M6.6 10.8c1.4 2.8 3.8 5.1 6.6 6.6l2.2-2.2c.3-.3.7-.4 1-.2 1.1.4 2.3.6 3.6.6.6 0 1 .4 1 1V20c0 .6-.4 1-1 1C10.6 21 3 13.4 3 4c0-.6.4-1 1-1h3.5c.6 0 1 .4 1 1 0 1.3.2 2.5.6 3.6.1.3 0 .7-.2 1z"/>
        </svg>
        587-412-9065
      </li>
      <li class="contact-item">
        <svg class="contact-icon" viewBox="0 0 24 24" aria-hidden="true">
          <circle cx="12" cy="12" r="10"/>
          <g fill="none" stroke="var(--card-black)" stroke-width="1.4">
            <ellipse cx="12" cy="12" rx="4.2" ry="10"/>
            <path d="M2 12h20M4 7h16M4 17h16"/>
          </g>
        </svg>
        colinvardek.ca
      </li>
    </ul>
  </main>
</body>
</html>
```